Web site for small printshop

I am looking for a website for small printshop in Iceland, mainly serving university students and artist.

We print posters, flyers, business cards and more.

In addition to our current website, I would like to include design tool, (fx. www.quarvelpad.example, www.trindomap.example or something similar) jobs upload, shopping chart.
Updates

Great work, I am really amazed of the quality of work i am seeing here.

Really way beyond my expectation

GOOD JOB - all of you ! 

Hi all.

The designs submitted have been great, way better than expected.
I really did not expect this level of quality.

Some have been asking me for feedback on their designs, and I will try 
to send some feedback here, without spoiling your creativity.

Likes:
- when the colors of my logo is used in menus, buttons etc.
- simple, not to crowded look.

Dislikes.
- Dark and heavy design
- Lot of text and buttons (crowded look)

Extra info.
- top line (before menus) will contain: Tel - email - language
- menu line will have 5 categories: Home - service - submission of works - FAQ - about us
- 3 large buttons:  Job submit - Job design - ask for offer

LOVE YOUR WORK - great designs so far :)

Target Market(s)

University Students, Artists. Age group 20-30

Industry/Entity Type

University

Requirements
Must have
• The website must be easy to use, clean looking.

```html
<!DOCTYPE html>
<html lang="en">
<head>
<meta charset="utf-8">
<title>Vellirprent – Printing Like Real</title>
<link href="https://fonts.googleapis.com/css2?family=Arimo:wght@400;700&family=Libre+Baskerville&display=swap" rel="stylesheet">
<style>
  :root {
    --yellow: #f7dc4f;
    --yellow-light: #fbe66b;
    --red: #e83a31;
    --green: #1f6b34;
    --ink: #1b1b1b;
    --muted: #8a8a8a;
    --page: #efeee9;
    --rule: #d8d7d1;
    --card: #ffffff;
    --dark-block: #222222;
  }
  * { box-sizing: border-box; margin: 0; padding: 0; }
  html, body { width: 882px; height: 1200px; overflow: hidden; }
  body {
    position: relative;
    background: var(--page);
    font-family: "Arimo", Arial, sans-serif;
    color: var(--ink);
  }
  .abs { position: absolute; }

  /* Top bar */
  .top-bar {
    left: 0; top: 0; width: 882px; height: 76px;
    background: linear-gradient(180deg, var(--yellow) 0%, var(--yellow-light) 100%);
  }
  .brand { left: 73px; top: 34px; display: flex; align-items: center; gap: 5px; }
  .brand-mark { width: 17px; height: 17px; background: var(--red); }
  .brand-name { font-weight: 700; font-size: 15px; color: var(--ink); letter-spacing: 0.2px; }
  .main-nav-active {
    left: 279px; top: 0; width: 99px; height: 76px; background: var(--red);
  }
  .main-nav-active-rule { left: 279px; top: 79px; width: 99px; height: 5px; background: var(--red); }
  .main-nav-item {
    top: 35px; font-weight: 700; font-size: 16.5px; color: var(--ink);
  }
  .main-nav-item.is-active { color: #fff; left: 305px; }

  /* Hero */
  .hero {
    left: 0; top: 76px; width: 882px; height: 270px;
    background: linear-gradient(180deg, #f4f4f4 0%, #ffffff 60%, #ececec 100%);
  }
  .hero-photo { top: 90px; height: 256px; }
  .hero-photo.left { left: 28px; width: 372px;
    background: radial-gradient(ellipse at 45% 40%, #2b2b2b 0%, #3a3a3a 35%, #e9e9e9 70%, #f4f4f4 100%); }
  .hero-photo.right { left: 455px; width: 405px;
    background: radial-gradient(ellipse at 55% 35%, #2b2b2b 0%, #4a2430 38%, #ececec 72%, #f4f4f4 100%); }
  .hero-title { left: 340px; top: 84px; font-weight: 700; font-size: 47px; letter-spacing: 0.5px; color: var(--ink); }
  .hero-like { left: 344px; top: 131px; font-size: 16px; color: var(--ink); }
  .hero-real { left: 370px; top: 151px; font-size: 31px; color: var(--red); }

  /* Secondary nav */
  .sub-nav-icon { left: 169px; top: 363px; }
  .sub-nav-item { top: 368px; font-size: 13px; color: var(--ink); }
  .rule { height: 1px; background: var(--rule); }

  /* Story */
  .section-heading { font-size: 18.5px; color: var(--ink); }
  .story-art {
    left: 190px; top: 448px; width: 96px; height: 107px;
    background: linear-gradient(135deg, #d9d9d9 0%, #2a2a2a 45%, #e0701d 60%, #f0f0f0 100%);
    transform: rotate(-10deg);
  }
  .body-copy { font-size: 9.4px; line-height: 15.3px; color: var(--ink); }

  .green-heading {
    left: 0; width: 882px; text-align: center;
    font-size: 18.5px; color: var(--green); letter-spacing: 0.3px;
  }

  /* Steps */
  .step-letter { left: 166px; top: 688px; font-size: 60px; color: var(--red); }
  .step-upload { left: 219px; top: 693px; font-weight: 700; font-size: 12.5px; }
  .step-upload-sub { left: 219px; top: 706px; font-family: "Libre Baskerville", Georgia, serif; font-size: 7.5px; color: var(--muted); }
  .step-select { left: 327px; top: 690px; font-size: 19px; }
  .step-select .accent { font-size: 12.5px; color: var(--red); }
  .size-select {
    left: 326px; top: 717px; width: 143px; height: 30px;
    background: #f7f7f4; border: 1px solid #cfcfca;
    font-size: 10px; color: #555;
  }
  .size-select span { position: absolute; left: 52px; top: 9px; }
  .size-select svg { position: absolute; right: 10px; top: 11px; }
  .step-pay { left: 513px; top: 733px; font-size: 12.5px; color: var(--ink); }

  /* Printer card */
  .card-corner-dark { left: 137px; top: 850px; width: 52px; height: 58px; background: var(--dark-block); }
  .card-corner-red { left: 692px; top: 1025px; width: 53px; height: 58px; background: var(--red); }
  .printer-card {
    left: 152px; top: 866px; width: 578px; height: 202px; background: var(--card);
    box-shadow: 0 1px 3px rgba(0,0,0,0.12);
  }
  .printer-art {
    left: 183px; top: 893px; width: 157px; height: 152px;
    background: linear-gradient(160deg, #e6e6e6 0%, #2f2f2f 45%, #1f8fd6 70%, #f2f2f2 100%);
  }

  /* Footer */
  .footer-text { left: 0; top: 1161px; width: 882px; text-align: center; font-size: 7px; font-weight: 700; color: var(--ink); }
  .footer-text .accent { color: var(--red); }
</style>
</head>
<body>

<header>
  <div class="abs top-bar"></div>
  <div class="abs brand"><span class="brand-mark"></span><span class="brand-name">VELLIRPRENT</span></div>
  <div class="abs main-nav-active"></div>
  <div class="abs main-nav-active-rule"></div>
  <nav>
    <span class="abs main-nav-item is-active">HOME</span>
    <span class="abs main-nav-item" style="left:403px">ABOUT US</span>
    <span class="abs main-nav-item" style="left:513px">PORTOFOLIO</span>
    <span class="abs main-nav-item" style="left:644px">CONTACT US</span>
  </nav>
</header>

<section>
  <div class="abs hero"></div>
  <div class="abs hero-photo left" role="img" aria-label="Photo of a black cylindrical printer printing a timeline document"></div>
  <div class="abs hero-photo right" role="img" aria-label="Photo of a black cylindrical printer printing maroon t-shirt designs"></div>
  <h1 class="abs hero-title">PRINTING</h1>
  <span class="abs hero-like">LIKE</span>
  <span class="abs hero-real">REAL</span>
</section>

<nav>
  <svg class="abs sub-nav-icon" width="20" height="19" viewBox="0 0 20 19" aria-hidden="true">
    <path d="M10 1 L19 9 L16.5 9 L16.5 18 L12 18 L12 12 L8 12 L8 18 L3.5 18 L3.5 9 L1 9 Z" fill="#e83a31"/>
  </svg>
  <span class="abs sub-nav-item" style="left:207px">HOME</span>
  <span class="abs sub-nav-item" style="left:300px">CATOGOREY</span>
  <span class="abs sub-nav-item" style="left:451px">ABOUT US</span>
  <span class="abs sub-nav-item" style="left:574px">BUY ONLINE</span>
</nav>
<div class="abs rule" style="left:131px; top:401px; width:584px"></div>

<section>
  <h2 class="abs section-heading" style="left:131px; top:419px">STORY BOARD</h2>
  <div class="abs story-art" role="img" aria-label="Illustration of a tilted photo with a paint brush and orange paint"></div>
  <p class="abs body-copy" style="left:315px; top:462px; width:380px">Pine Stall sprouted from a hot dog cart in Linden Court Park in Eastbrook cre-ated by Tomas Reyl's Harbor Row Dining Group (HRDG) to support the Linden Court Park Trust's first art installation. The cart was quite the success, with Stall Fans lined up daily for three summers.</p>
</section>
<div class="abs rule" style="left:131px; top:566px; width:584px"></div>

<section>
  <h2 class="abs green-heading" style="top:587px">HOW CAN YOU CONTACT US</h2>
  <div class="abs rule" style="left:131px; top:625px; width:584px"></div>

  <span class="abs step-letter">U</span>
  <span class="abs step-upload">PLOAD</span>
  <span class="abs step-upload-sub">YOUR FILES</span>
  <svg class="abs" style="left:238px; top:716px" width="74" height="34" viewBox="0 0 74 34" aria-hidden="true">
    <rect x="0" y="11" width="4" height="12" fill="#222"/>
    <rect x="7" y="11" width="4" height="12" fill="#222"/>
    <rect x="14" y="11" width="4" height="12" fill="#222"/>
    <rect x="21" y="11" width="22" height="12" fill="#222"/>
    <path d="M43 2 L72 17 L43 32 Z" fill="#222"/>
  </svg>

  <span class="abs step-select">SELECT <span class="accent">THE SIZE</span></span>
  <div class="abs size-select">
    <span>A3</span>
    <svg width="10" height="7" viewBox="0 0 10 7" aria-hidden="true"><path d="M1 1 L5 5 L9 1" stroke="#333" stroke-width="1.6" fill="none"/></svg>
  </div>
  <svg class="abs" style="left:483px; top:694px" width="44" height="20" viewBox="0 0 44 20" aria-hidden="true">
    <rect x="0" y="6" width="3" height="8" fill="#222"/>
    <rect x="5" y="6" width="3" height="8" fill="#222"/>
    <rect x="10" y="6" width="3" height="8" fill="#222"/>
    <rect x="15" y="6" width="13" height="8" fill="#222"/>
    <path d="M28 1 L43 10 L28 19 Z" fill="#222"/>
  </svg>

  <svg class="abs" style="left:648px; top:677px" width="46" height="46" viewBox="0 0 46 46" aria-hidden="true">
    <circle cx="23" cy="23" r="22" fill="#e83a31"/>
    <path d="M13 23 L20 30 L33 15" stroke="#fff" stroke-width="4.5" fill="none" stroke-linecap="round" stroke-linejoin="round"/>
  </svg>
  <span class="abs step-pay">AND PAY THE LOWEST COST</span>
</section>
<div class="abs rule" style="left:131px; top:790px; width:584px"></div>

<section>
  <h2 class="abs green-heading" style="top:812px">3: OUR SELECTING USED PRINTER</h2>
  <div class="abs card-corner-dark"></div>
  <div class="abs card-corner-red"></div>
  <div class="abs printer-card"></div>
  <div class="abs printer-art" role="img" aria-label="Illustration of a blue and black desktop inkjet printer with paper"></div>
  <h3 class="abs section-heading" style="left:369px; top:906px; font-weight:400">STORY BOARD</h3>
  <p class="abs body-copy" style="left:367px; top:948px; width:330px">Pine Stall sprouted from a hot dog cart in Linden Court Park in East-brook created by Tomas Reyl's Harbor Row Dining Group (HRDG) to support the Linden Court Park Trust's first art installation. The cart was quite the success, with Stall Fans lined up daily for three sum-mers.</p>
</section>

<footer>
  <div class="abs rule" style="left:353px; top:1141px; width:199px"></div>
  <p class="abs footer-text">ALLRIGHTS RESERVED BY <span class="accent">COMPANY NAME</span>@THE DATE</p>
</footer>

</body>
</html>
```